Professional and creative business card design for recruiting service providers

Our company supports German medium-sized companies in filling vacancies promptly. For this we use social media marketing and bring our customers into the visibility.

We want a professional but also creative design for our business cards.

Please look at lindqvar-staff.de to get an impression of our CI.

Target Market(s)

Small and medium-sized companies in Germany from the industry

Industry/Entity Type

Industrie, Handwerk

Contact Information for Business Card

Name, Position, Telefonnummer, Email, Website

Colors
EE7325
F08F49
F5BC92
FAE3D3
FDF4ED

Requirements
Must have
• A picture of the employee and in the style of www.lindqvar-staff.de

```html
<!DOCTYPE html>
<html lang="de">
<head>
<meta charset="utf-8">
<title>Lindqvar &amp; Staff – Visitenkarte</title>
<link href="https://fonts.googleapis.com/css2?family=Montserrat:wght@400;500;600;700&display=swap" rel="stylesheet">
<style>
  :root {
    --orange: #EE6A31;
    --ink: #262626;
    --white: #ffffff;
    --card-dark: #141414;
    --stage: #1e1e1e;
    --photo-glow: #5c5c5c;
    --photo-mid: #2e2e2e;
    --photo-suit: #23252c;
    --photo-dark: #141414;
  }
  * { margin: 0; padding: 0; box-sizing: border-box; }
  html, body { width: 1200px; height: 1059px; overflow: hidden; }
  body {
    background: var(--stage);
    font-family: "Montserrat", sans-serif;
    position: relative;
  }
  .card {
    position: absolute;
    border-radius: 24px;
    overflow: hidden;
  }
  .card--front { left: 256px; top: 89px; width: 688px; height: 390px; background: var(--white); }
  .card--back { left: 254px; top: 546px; width: 693px; height: 394px; background: var(--card-dark); }

  .brand { position: absolute; display: flex; align-items: center; gap: 16px; z-index: 1; }
  .brand__square { width: 40px; height: 40px; background: var(--orange); flex: none; }
  .brand__name {
    font-weight: 700; font-size: 27px; line-height: 30px; letter-spacing: 1.5px;
    text-transform: uppercase;
  }
  .card--front .brand { left: 62px; top: 160px; }
  .card--front .brand__name { color: var(--ink); }
  .card--back .brand { left: 41px; top: 48px; }
  .card--back .brand__name { color: var(--white); font-size: 29px; line-height: 32px; }

  .divider { position: absolute; left: 344px; top: 130px; width: 1.5px; height: 134px; background: var(--orange); }

  .person { position: absolute; left: 373px; top: 124px; }
  .person__name { color: var(--orange); font-weight: 700; font-size: 22px; letter-spacing: 0.6px; line-height: 26px; text-transform: uppercase; }
  .person__role { color: var(--ink); font-weight: 600; font-size: 16px; line-height: 20px; }

  .contact { position: absolute; left: 373px; top: 192px; list-style: none; }
  .contact__item { display: flex; align-items: center; gap: 7px; height: 27px; color: var(--ink); font-size: 16px; font-weight: 400; letter-spacing: 0.3px; }
  .contact__icon { width: 12px; height: 12px; flex: none; }
  .contact__icon--fill { fill: var(--orange); }
  .contact__icon--line { fill: none; stroke: var(--orange); stroke-width: 2; }

  .portrait {
    position: absolute; right: 0; top: 0; width: 390px; height: 100%;
    background:
      radial-gradient(ellipse 38% 30% at 62% 26%, var(--photo-glow), transparent 100%),
      linear-gradient(to bottom, var(--photo-mid) 0%, var(--photo-mid) 45%, var(--photo-suit) 70%, var(--photo-suit) 100%);
    -webkit-mask-image: linear-gradient(to right, transparent 0%, #000 22%);
    mask-image: linear-gradient(to right, transparent 0%, #000 22%);
  }
</style>
</head>
<body>
  <section class="card card--front">
    <div class="brand">
      <span class="brand__square"></span>
      <span class="brand__name">Lindqvar<br>&amp; Staff</span>
    </div>
    <div class="divider"></div>
    <div class="person">
      <p class="person__name">Jonas Lindqvar</p>
      <p class="person__role">Gründer</p>
    </div>
    <ul class="contact">
      <li class="contact__item">
        <svg class="contact__icon contact__icon--fill" viewBox="0 0 24 24"><path d="M6.6 10.8a15.1 15.1 0 0 0 6.6 6.6l2.2-2.2a1 1 0 0 1 1-.25 11.4 11.4 0 0 0 3.6.57 1 1 0 0 1 1 1V20a1 1 0 0 1-1 1A17 17 0 0 1 3 4a1 1 0 0 1 1-1h3.5a1 1 0 0 1 1 1c0 1.25.2 2.45.57 3.57a1 1 0 0 1-.25 1z"/></svg>
        (123) 456 7890
      </li>
      <li class="contact__item">
        <svg class="contact__icon" viewBox="0 0 24 24"><rect x="2" y="5" width="20" height="14" fill="#EE6A31"/><path d="M2 5l10 8 10-8" fill="none" stroke="#ffffff" stroke-width="2"/></svg>
        info@lindqvar-staff.de
      </li>
      <li class="contact__item">
        <svg class="contact__icon contact__icon--line" viewBox="0 0 24 24"><circle cx="12" cy="12" r="10"/><path d="M2 12h20M12 2c3 3 3 17 0 20M12 2c-3 3-3 17 0 20"/></svg>
        www.lindqvar-staff.de
      </li>
    </ul>
  </section>

  <section class="card card--back">
    <div class="brand">
      <span class="brand__square"></span>
      <span class="brand__name">Lindqvar<br>&amp; Staff</span>
    </div>
    <div class="portrait" role="img" aria-label="Porträtfoto des Gründers in dunklem Sakko und Rollkragenpullover vor dunkelgrauem Hintergrund"></div>
  </section>
</body>
</html>
```